Website front end design for an education nonprofit

This project involves design and development of the website front end (i.e., Web user interface and user experience design) for TAVO Sphere, a nonprofit initiative for developing an online platform for basic English language instruction, especially targeted toward underprivileged, non-native English speaking populations.

More about us: We are a team of educators, researchers and engineers passionate about this cause and would like to invite talented, creative web developers to join us in this effort to create positive social impact! Please send a personal message to the project owner for the executive summary to get more information about our initiative, big picture vision and the team.

TAVO Sphere website front end (UI/UX) design
Our key goals for this project are to develop an impressive Drupal-based front end for our website as well as to find really talented and creative web/UI/UX designers-cum-developers who are experts in the state-of-the-art web technologies, and are passionate about the cause of global online basic education. At the end of this project, we hope to have long term engagement with the selected developer(s) for our future website design and development needs.

Here are some preliminary guidelines on the TAVO Sphere website front end framework as envisioned by us so far. Please note that we would very much encourage creative ideas and mock-ups from the developers.

1. Current platform: Our website prototype back-end uses Drupal CMS (we plan to continue using Drupal CMS) and at the moment, a toy front-end is based on the Drupal Skeleton platform for its simplicity, clean UI and mobile device friendliness. The web developer / designer can choose any Drupal front end as a starting point or come up with a new Drupal template that meets our requirements below. Prior experience and expertise on Drupal would be great.

2. Audience profile: While the primary audience for the website is expected to be young kids (6-10 years) not very familiar with English, the secondary audience also includes adults interested in basic English language skills. So the overall goal is to have simple, uncluttered / clean, elegant and lightweight (think loading time as well as mobile device friendliness) interface that is extremely intuitive and easy to navigate, is artistic and aesthetically appealing to a wide audience (especially the non-native English speaking populations). The most important point is that our target audience should feel welcome with the clean, crisp look and easy, user-centric navigation, and should in no case feel overwhelmed (say with too much text or clutter on the front page).

3. Front page: Here is a currently envisioned preliminary sketch of the website front page (very much open for refinement and improvements)
a. The top “menu bar” part of the landing page will have our organization name and logo along with (or above) the top menu bar with the following links and sub-links
i. “Learn” link with sub-menu of all our content sections (World learning, Basic sentence learning, Classic short stories, Picture Dictionary)
ii. “About” links with information about us (sub-menu entries: About TAVO Sphere, Team, Supporters, Contributors)
iii. “Contribute” link with sub-menu entries Donate, Volunteer
iv. Menu entries towards the right side: “Login / sign up” followed by
v. “Search” with space to enter the search phrase
b. The middle “main page content” part of the page is where we would have entry points to our main content categories. The portion is envisioned to be graphical, with big blocks (images) as links to our content categories. The current categories (to start with) include 1. Word learning, 2. Basic sentence learning, and 3. Classic stories. We welcome creative ideas to represent these content categories in an appealing and elegant way (for example, these content categories could be portrayed as closed double doors that lead to the pages with the content. We would like to have placeholders for appropriate image links to different content categories – we should be able to put appropriate images or change them as we come up with new ideas that would work best with our target audience). The categories would change and grow as our content evolves, hence the core idea is to build a flexible framework that readily allows for expansion as well as customization.
c. The bottom menu / links bar portion of the landing page will have a list of links that are not included at the top. Examples include (with flexibility needed to add more when needed)
i. “Help”: this leads to a new page with FAQ, How to use
ii. “Contact us” link to a web contact form page
iii. “For Teachers” link to a page with information such as how to use, tips, pilot programs,
iv. “Volunteer” link to page with links such as Donate, Volunteer
v. “Contributors” that would link to a page with information about our Artists, Teachers, Writers, Developers etc.
vi. “Jobs” would link to a jobs page
vii. “Blog” would lead to our blog page
viii. “User stories” link to pages with feedback that we obtain from the users about how the content has helped them,
ix. Web 2.0 placeholders for social media (to be added later)

d. The footer of the website should include text “2013 TAVO Sphere, All rights reserved.”

4. The middle block of the front page is the largest in screen real estate and perhaps the most challenging part that requires much creativity and thought on the UI/UX design aspect – the content pages pointed to by the section links on the middle portion of the front page are also being designed.

5. Color preference is towards soft, elegant (think grays, whites, light blues, other light colors) web safe colors. No harsh (too bright, garish) colors.

6. Fonts preference Nice, clean looking fonts (Arial alright) compatible across browsers.

7. Portability and robustness of the front page layout for different platforms should be carefully considered. Although our first launch target platform is PC (where cross browser compatibility is important), this would very soon be followed by mobile devices such as tablets and smartphones given their prevalence across the globe. This mobile friendly design or easy portability to mobile platforms with little work requirement should be considered as a design requirement.

8. Front page as a framework for the complete website: Note that the top and the bottom portions of the front page are envisioned be used as a common template / frame across all the pages of our website – the middle portion would be used to show our content on the other pages of our website.

9. UX: For the UI/UX design, it is critical to keep in mind key qualities such as ease of use, simplicity, elegance and artistic appeal. Some specific points to keep in mind: (1) the major portion of the target audience would be new to English and (2) young children are expected to be the primary audience but we want the website to appeal to adults interested in learning as well, and (3) we need the website to work even with relatively slow Internet speeds (for underdeveloped / developing regions especially), should always be kept in mind. HTML5 compliance ideas are encouraged.

10. Strictly not desired: Typical corporate feel seen in many webpages, blocky graphics, dull and uninviting overall look with no personality, Flash type effects, harsh colors.

11. Creativity and imagination necessary: We would like to reiterate that the designer/developer has complete freedom to re-imagine the front page considering the above requirements and get back with ideas for an inspiring layout that presents the content outlined above in an intuitive format, carefully considering our target audience.

A note: As a rule, we will always make sure that our developers and artists get proper credit for their work and are recognized and acknowledged by everyone visiting our website.

Expected deliverables:
Website design psd files AND coded webpage / Drupal template: the corresponding source code and all the required libraries, images etc would be required with minimal documentation / pointers on how to make changes and customizations.

Interested developers are encouraged to first send us preliminary prototype Design for the front page to get feedback on whether their approach and style is in line with our needs and preferences. We will suggest the developers to proceed further if the team thinks there is some potential for a match (of course, the final determination would be from the pool of shortlisted submissions) – otherwise, in case the team does not see potential for a match with our needs or if we have already received multiple submissions that are comparatively more closely aligned with our vision for the website, we'd prefer to be respectful of the developers’ time and effort by requesting them not to proceed further.

Please consider this effort as your contribution to an important social cause of global and accessible online education and not a commercial enterprise (our passion for making a positive impact is what is driving the TAVO Sphere nonprofit team to undertake this initiative!). We would like to invite you to join us in this effort!

Project Deadline Extended
Reason: Due to requests from interested designers, we are extending the deadline. Looking forward to receiving many other creative designs!

Please see the project brief.

Real Estate

• Please see the project brief.

```html
<!DOCTYPE html>
<html lang="en">
<head>
<meta charset="utf-8">
<title>TAVO Sphere – Learn English</title>
<link rel="stylesheet" href="https://fonts.googleapis.com/css2?family=Arimo:wght@400;700&display=swap">
<style>
  :root{
    --ink:#3a3a3a;
    --muted:#6b6b6b;
    --page:#e6e7e9;
    --panel:#ffffff;
    --top-dark:#1c1c1e;
    --top-dark-2:#2e2f31;
    --blue:#2a9fd8;
    --blue-deep:#1a7db8;
    --blue-soft:rgba(34,140,205,.85);
    --footer:#2a2b2d;
    --footer-line:#3c3d40;
    --footer-text:#c4c4c4;
    --btn:#4a4a4a;
  }
  *{box-sizing:border-box;margin:0;padding:0}
  html,body{width:885px;height:1200px;overflow:hidden}
  body{font-family:"Arimo",Arial,sans-serif;color:var(--ink);background:var(--page);position:relative}

  /* top bar */
  .topbar{height:83px;background:linear-gradient(#2a2b2d,var(--top-dark));display:flex;align-items:center;justify-content:space-between;padding:0 40px 0 40px}
  .brand{display:flex;align-items:center;gap:10px;color:#fff;font-weight:700;font-size:26px;letter-spacing:.5px}
  .brand-dot{width:14px;height:14px;border-radius:50%;background:var(--blue)}
  .callout{color:#fff;font-size:13px}
  .callout strong{font-size:19px;letter-spacing:.5px;margin-left:4px}

  /* nav */
  .nav{height:41px;background:linear-gradient(var(--blue),var(--blue-deep));display:flex;align-items:center;padding:0 0 0 108px}
  .nav-links{display:flex;gap:46px;list-style:none}
  .nav-links a{color:#fff;text-decoration:none;font-size:13px;font-weight:700;letter-spacing:.5px}
  .search{margin-left:auto;display:flex;align-items:center;width:150px;height:20px;background:#fff;border-radius:2px;padding:0 6px;justify-content:space-between;margin-right:18px}
  .search span{font-size:10px;color:#999}
  .account{display:flex;height:41px}
  .account a{display:flex;align-items:center;gap:6px;padding:0 14px;color:#fff;text-decoration:none;font-size:12px;font-weight:700;background:rgba(0,0,0,.18);border-left:1px solid rgba(255,255,255,.2)}
  .account a:last-child{margin-right:103px}

  /* hero */
  .hero{position:relative;height:324px;background:linear-gradient(100deg,#b9c7d3 0%,#dfe3e6 30%,#e9dccf 55%,#c6d2dc 80%,#a9bccb 100%)}
  .hero-arrows{position:absolute;left:86px;top:205px;display:flex;gap:6px}
  .hero-arrows span{width:26px;height:26px;border-radius:50%;background:#333;display:flex;align-items:center;justify-content:center}
  .hero-caption{position:absolute;right:0;top:208px;width:326px;height:48px;background:var(--blue-soft);color:#fff;font-size:19px;display:flex;align-items:center;padding-left:22px;letter-spacing:.3px}

  /* main panel */
  .panel{position:absolute;left:103px;top:448px;width:679px;height:438px;background:var(--panel);box-shadow:0 0 6px rgba(0,0,0,.08);text-align:center}
  .welcome h1{margin-top:12px;font-size:21px;color:var(--blue);font-weight:700;letter-spacing:.5px}
  .welcome h2{font-size:13px;font-weight:700;margin-top:8px;color:#444}
  .welcome p{font-size:10.5px;line-height:15px;color:var(--muted);width:600px;margin:8px auto 0}
  .more{display:inline-flex;align-items:center;gap:5px;margin-top:10px;background:var(--btn);color:#fff;font-size:10px;padding:4px 6px 4px 10px;border-radius:10px;text-decoration:none}
  .more i{width:12px;height:12px;border-radius:50%;background:#fff;display:flex;align-items:center;justify-content:center}
  .rule{height:1px;background:#e3e3e3;margin:16px 14px 0}
  .cards{display:flex;justify-content:space-between;padding:14px 16px 0}
  .card{width:204px}
  .card-img{height:138px;border:3px solid #fff;box-shadow:0 0 4px rgba(0,0,0,.25)}
  .card h3{font-size:12px;font-weight:700;margin-top:10px;color:#444}
  .card p{font-size:9.5px;line-height:13px;color:var(--muted);margin-top:5px}

  /* action band */
  .actions{position:absolute;left:0;top:890px;width:885px;height:56px;background:linear-gradient(var(--blue),var(--blue-deep));display:flex}
  .action{flex:1;display:flex;align-items:center;justify-content:center;gap:14px;color:#fff}
  .action + .action{border-left:1px solid rgba(255,255,255,.35)}
  .action-icon{width:40px;height:34px;border-radius:6px}
  .action small{font-size:10px;font-style:normal}
  .action b{font-size:17px;letter-spacing:.5px}
  .action em{font-size:9px;font-style:normal;display:block;opacity:.9}

  /* footer */
  .footer{position:absolute;left:0;top:946px;width:885px;height:254px;background:var(--footer);color:var(--footer-text)}
  .footer-cols{display:flex;padding:18px 0 0 103px;gap:0}
  .footer h4{color:#fff;font-size:13px;font-weight:400;margin-bottom:10px}
  .col-links{width:263px}
  .col-links ul{list-style:none;display:grid;grid-template-columns:120px 120px;row-gap:8px;font-size:10px}
  .col-links li{padding-left:10px;position:relative}
  .col-links li:before{content:"";position:absolute;left:0;top:4px;border-left:4px solid var(--blue);border-top:3px solid transparent;border-bottom:3px solid transparent}
  .col-social{width:242px}
  .social{display:flex;gap:6px;margin-bottom:18px}
  .social span{width:20px;height:20px;border-radius:50%;background:var(--blue)}
  .social span:nth-child(2){background:#3b5b93}
  .social span:nth-child(3){background:#5b8fc7}
  .social span:nth-child(4){background:#e08a2c}
  .col-social p{font-size:10px;margin-bottom:8px}
  .field{background:#fff;height:20px;border-radius:2px;font-size:9px;color:#888;padding:5px 6px}
  .news{width:190px}
  .news-row{display:flex;align-items:center;gap:6px}
  .news-row .field{flex:1}
  .join,.send{background:#4a4a4a;color:#fff;font-size:9px;padding:4px 12px;border:1px solid #666;display:inline-block}
  .join{margin:8px 0 0 70px}
  .col-contact{width:180px}
  .col-contact .field{margin-bottom:8px}
  .area{height:58px}
  .send{float:right}
  .copyright{position:absolute;left:0;bottom:0;width:885px;height:26px;border-top:1px solid var(--footer-line);font-size:9px;display:flex;align-items:center;justify-content:center;color:#aaa;background:#232425}
</style>
</head>
<body>

<header class="topbar">
  <div class="brand"><span class="brand-dot"></span>TAVO Sphere</div>
  <div class="callout">Call us Today! <strong>1800-555-0142</strong></div>
</header>

<nav class="nav">
  <ul class="nav-links">
    <li><a href="#">LEARN</a></li>
    <li><a href="#">ABOUT</a></li>
    <li><a href="#">CONTRIBUTE</a></li>
  </ul>
  <div class="search"><span>Search</span>
    <svg width="10" height="10" viewBox="0 0 10 10"><circle cx="4" cy="4" r="3" fill="none" stroke="#888" stroke-width="1.4"/><line x1="6.2" y1="6.2" x2="9.3" y2="9.3" stroke="#888" stroke-width="1.4"/></svg>
  </div>
  <div class="account">
    <a href="#"><svg width="10" height="10" viewBox="0 0 10 10"><rect x="1.5" y="4.5" width="7" height="5" fill="#fff"/><path d="M3 4.5V3a2 2 0 0 1 4 0v1.5" fill="none" stroke="#fff" stroke-width="1.2"/></svg>LOGIN</a>
    <a href="#"><svg width="10" height="10" viewBox="0 0 10 10"><rect x="0.5" y="0.5" width="9" height="9" fill="none" stroke="#fff"/><path d="M3 5h4M5 3v4" stroke="#fff"/></svg>SIGN UP</a>
  </div>
</nav>

<section class="hero" role="img" aria-label="Photo of a young girl studying at a classroom desk with classmates behind her">
  <div class="hero-arrows">
    <span><svg width="10" height="10" viewBox="0 0 10 10"><path d="M6.5 1.5L3 5l3.5 3.5" fill="none" stroke="#fff" stroke-width="1.6"/></svg></span>
    <span><svg width="10" height="10" viewBox="0 0 10 10"><path d="M3.5 1.5L7 5 3.5 8.5" fill="none" stroke="#fff" stroke-width="1.6"/></svg></span>
  </div>
  <div class="hero-caption">BASIC SENTENCE LEARNING</div>
</section>

<main class="panel">
  <section class="welcome">
    <h1>WELCOME</h1>
    <h2>The standard Lorem Ipsum passage</h2>
    <p>Simple lessons in English for every child and adult. Learn new words, build basic sentences and enjoy classic short stories at your own pace, anywhere and on any device, even on slow connections.</p>
    <a class="more" href="#">Read more <i><svg width="6" height="6" viewBox="0 0 6 6"><path d="M2 1l2 2-2 2" fill="none" stroke="#4a4a4a" stroke-width="1.2"/></svg></i></a>
  </section>
  <div class="rule"></div>
  <section class="cards">
    <article class="card">
      <div class="card-img" role="img" aria-label="Photo of a teacher helping two children at a computer" style="background:linear-gradient(135deg,#d9cfc3,#9fb3c4)"></div>
      <h3>FOR TEACHERS</h3>
      <p>Tips, guides and pilot programs to bring our lessons into your classroom.</p>
      <a class="more" href="#">Read more <i><svg width="6" height="6" viewBox="0 0 6 6"><path d="M2 1l2 2-2 2" fill="none" stroke="#4a4a4a" stroke-width="1.2"/></svg></i></a>
    </article>
    <article class="card">
      <div class="card-img" role="img" aria-label="Photo of a child reading a book outdoors on the grass" style="background:linear-gradient(135deg,#a9c27a,#e3d3a6)"></div>
      <h3>USER STORIES</h3>
      <p>Real stories from learners about how simple daily lessons helped them grow.</p>
      <a class="more" href="#">Read more <i><svg width="6" height="6" viewBox="0 0 6 6"><path d="M2 1l2 2-2 2" fill="none" stroke="#4a4a4a" stroke-width="1.2"/></svg></i></a>
    </article>
    <article class="card">
      <div class="card-img" role="img" aria-label="Photo of a boy writing at a desk with books" style="background:linear-gradient(135deg,#e6c9a0,#b7c8d6)"></div>
      <h3>CONTRIBUTORS</h3>
      <p>Meet the artists, teachers, writers and developers who build every lesson.</p>
      <a class="more" href="#">Read more <i><svg width="6" height="6" viewBox="0 0 6 6"><path d="M2 1l2 2-2 2" fill="none" stroke="#4a4a4a" stroke-width="1.2"/></svg></i></a>
    </article>
  </section>
</main>

<section class="actions">
  <div class="action">
    <div class="action-icon" role="img" aria-label="Heart illustration for donations" style="background:#e0564f"></div>
    <small>Click here</small>
    <div><b>DONATE NOW</b><em>Help a child learn today</em></div>
  </div>
  <div class="action">
    <div class="action-icon" role="img" aria-label="Illustration of a group of volunteers" style="background:linear-gradient(90deg,#f0b23a,#7cc24d)"></div>
    <small>Click here</small>
    <div><b>VOLUNTEER</b><em>Share your time and skills</em></div>
  </div>
</section>

<footer class="footer">
  <div class="footer-cols">
    <div class="col-links">
      <h4>Quick links</h4>
      <ul>
        <li>Home</li><li>Volunteer</li>
        <li>About Us</li><li>Contributors</li>
        <li>Help</li><li>Jobs</li>
        <li>Contact Us</li><li>Blog</li>
        <li>For teachers</li><li>User stories</li>
      </ul>
    </div>
    <div class="col-social">
      <h4>Follow Us</h4>
      <div class="social" aria-label="Social media links"><span></span><span></span><span></span><span></span></div>
      <h4>Newsletter Sign</h4>
      <div class="news">
        <p>Sign up for email updates</p>
        <div class="field">Enter your email</div>
        <span class="join">JOIN</span>
      </div>
    </div>
    <div class="col-contact">
      <h4>Contact Us</h4>
      <div class="field">Name</div>
      <div class="field area">Your Message</div>
      <span class="send">SEND ME</span>
    </div>
  </div>
  <div class="copyright">© 2013 TAVO Sphere, All rights reserved.</div>
</footer>

</body>
</html>
```